Email Signature Design

Please design an email signature, the below is an example of our current design;
___

HARCOURT ESTATE PARTNERS PTY LTD
DOMINIC FARRADAY
Licensed Strata and Community Manager

148 Calloway Street,
HAWTHORNE NSW 2041

P: 02.9374.6082 F: 9463.7820
Website: www.harcourtestate.com.au

This e-mail message and accompanying data may contain information that is confidential and private. If you are not the intended recipient, the use, dissemination, distribution or copying of this message or data is prohibited.

If you have received this e-mail in error please notify us immediately and delete all material pertaining to this e-mail. strata@harcourtestate.com.au

___

We would like to incorporate our logo and company colours, you can view the colours and feel of image at www.harcourtestate.com.au

Industry/Entity Type

It Company

Requirements
Must have
• use of logo and company colours (image)

```html
<!DOCTYPE html>
<html lang="en">
<head>
<meta charset="utf-8">
<title>Harcourt Estate Partners – Email Signature</title>
<link rel="stylesheet" href="https://fonts.googleapis.com/css2?family=Arimo:wght@400;700&display=swap">
<style>
  :root {
    --olive: #8b7c36;
    --sand: #e3d4b4;
    --slate: #6e6e6e;
    --ink: #4a4a4a;
    --muted: #5c5c5c;
    --rule: #9a9a9a;
    --paper: #ffffff;
  }
  * { margin: 0; padding: 0; box-sizing: border-box; }
  html, body {
    width: 1200px;
    height: 1000px;
    overflow: hidden;
    background: var(--paper);
    font-family: "Arimo", Arial, sans-serif;
    color: var(--ink);
  }
  .signature {
    position: absolute;
    left: 160px;
    top: 250px;
    width: 880px;
  }
  .sender-name {
    font-size: 29px;
    font-weight: 700;
    color: var(--olive);
    letter-spacing: 0.3px;
  }
  .sender-role {
    font-size: 20px;
    color: var(--slate);
    margin-top: 2px;
  }
  .brand-block {
    display: flex;
    align-items: flex-start;
    margin-top: 44px;
  }
  .brand-mark-area {
    width: 128px;
    height: 134px;
    flex: none;
    display: flex;
    align-items: center;
    justify-content: flex-start;
  }
  .brand-square {
    width: 84px;
    height: 84px;
    background: var(--sand);
    border-left: 12px solid var(--olive);
  }
  .brand-text { margin-left: 40px; }
  .brand-name {
    font-size: 41px;
    font-weight: 700;
    color: var(--slate);
    letter-spacing: 0.5px;
    line-height: 1.05;
  }
  .brand-tagline {
    font-size: 30px;
    color: var(--slate);
    letter-spacing: 0.6px;
    margin-top: 4px;
  }
  .contact {
    display: flex;
    margin-top: 16px;
    font-size: 16px;
    color: var(--muted);
    line-height: 1.3;
  }
  .contact-lines { padding-right: 18px; border-right: 1.5px solid var(--rule); }
  .contact-address { padding-left: 18px; }
  .label { color: var(--olive); font-weight: 700; }
  .web strong { color: var(--olive); font-weight: 700; }
  .disclaimer {
    margin-top: 42px;
    font-size: 15.5px;
    color: var(--muted);
    line-height: 1.35;
  }
  .disclaimer p + p { margin-top: 20px; }
</style>
</head>
<body>
  <div class="signature">
    <div class="sender-name">DOMINIC FARRADAY</div>
    <div class="sender-role">Licensed Strata and Community Manager</div>

    <div class="brand-block">
      <div class="brand-mark-area">
        <div class="brand-square"></div>
      </div>
      <div class="brand-text">
        <div class="brand-name">HARCOURT ESTATE PARTNERS</div>
        <div class="brand-tagline">STRATA MANAGEMENT SERVICES</div>
        <div class="contact">
          <div class="contact-lines">
            <div><span class="label">P:</span> 02.9374.6082 <span class="label">F:</span> 9463.7820</div>
            <div class="web">www.<strong>harcourtestate</strong>.com.au</div>
          </div>
          <div class="contact-address">
            <div>148 Calloway Street,</div>
            <div>HAWTHORNE NSW 2041</div>
          </div>
        </div>
      </div>
    </div>

    <div class="disclaimer">
      <p>This e-mail message and accompanying data may contain information that is confidential and private.<br>
      If you are not the intended recipient, the use, dissemination, distribution or copying of this message or data is prohibited.</p>
      <p>If you have received this e-mail in error please notify us immediately and delete all material<br>
      pertaining to this e-mail. strata@harcourtestate.com.au</p>
    </div>
  </div>
</body>
</html>
```